Gemstones e-commerce web-site needs a new template/style

We would like to highlight some of our more exclusive product (gemstones) in a new signature template that has its own style, fonts and colors. The new template would allow for larger and more detailed images. e.g. Tovelcrest.com. The design should account for different sized mobile devices. Current site is http://www.kelvorastones.com

Industry/Entity Type

Product

Number of Pages Required

2 page

```html
<!DOCTYPE html>
<html lang="en">
<head>
<meta charset="utf-8">
<title>Kelvora Stones – Stones</title>
<link rel="stylesheet" href="https://fonts.googleapis.com/css2?family=Cinzel:wght@400&family=Crimson+Text:wght@400&family=Open+Sans:wght@400;600&family=Pinyon+Script&display=swap">
<style>
:root{
  --bg:#0f0f0f;
  --header:#121212;
  --nav:#050505;
  --footer:#161616;
  --bottom:#0b0b0b;
  --text:#e6e6e6;
  --muted:#8d8d8d;
  --dim:#5e5e5e;
  --green:#2f9a3e;
  --line:#6a6a6a;
}
*{box-sizing:border-box;margin:0;padding:0}
html,body{width:737px;height:1200px;overflow:hidden;background:var(--bg)}
body{position:relative;font-family:"Open Sans",sans-serif;color:var(--text)}
.abs{position:absolute}

/* header */
.site-header{position:absolute;left:0;top:0;width:737px;height:68px;background:var(--header)}
.brand{left:62px;top:24px;display:flex;align-items:center;gap:7px}
.brand-mark{width:9px;height:9px;background:#cfcfcf}
.brand-name{font-family:"Crimson Text",serif;font-size:16px;color:var(--text);letter-spacing:.3px}
.shipping{left:260px;top:19px;width:132px;height:32px;border:1px solid #444;display:flex;align-items:center;justify-content:center;gap:8px;font-family:"Cinzel",serif;font-size:10px;letter-spacing:.5px}
.top-links{right:75px;top:19px;font-size:6px;letter-spacing:.8px;color:var(--muted);display:flex;gap:9px}
.social-row{left:413px;top:40px;display:flex;align-items:center;gap:10px;font-size:8px}
.social-name{color:#fff;font-weight:600}
.phone{color:var(--muted);font-size:6px;letter-spacing:.6px;display:flex;align-items:center;gap:5px}
.cart{color:var(--muted);font-size:6px;letter-spacing:.7px;display:flex;align-items:center;gap:6px;margin-left:6px}

.main-nav{position:absolute;left:0;top:68px;width:737px;height:23px;background:var(--nav);display:flex;justify-content:center;align-items:center;gap:13px;font-family:"Crimson Text",serif;font-size:7.5px;letter-spacing:.4px}
.main-nav .dot{width:3px;height:3px;border-radius:50%;background:#ddd}

/* hero */
.hero{left:0;top:91px;width:737px;height:166px;background:radial-gradient(ellipse at 75% 55%,#6e6e6e 0%,#2e2e2e 28%,#121212 60%),#111}
.hero-title{left:122px;top:118px;font-family:"Crimson Text",serif;font-size:14px;letter-spacing:.5px}
.hero-script{left:70px;top:155px;width:240px;text-align:center;font-family:"Pinyon Script",cursive;font-size:19px;line-height:23px;color:#eee}
.hero-market{left:128px;top:217px;font-size:8px;display:flex;align-items:center;gap:6px}
.hero-market b{font-size:13px;font-weight:600;color:#eee}

/* listing */
.section-title{left:61px;top:288px;font-family:"Cinzel",serif;font-weight:400;font-size:21px;color:var(--green);letter-spacing:1px}
.section-intro{left:61px;top:322px;font-size:6.2px;color:var(--muted)}

.card{position:absolute;width:113px}
.card-img{width:113px;height:113px}
.card-code{margin-top:8px;text-align:center;font-family:"Crimson Text",serif;font-weight:400;font-size:9px}
.card-desc{margin-top:6px;padding-left:4px;font-size:5.2px;line-height:11px;color:var(--muted);letter-spacing:.2px}
.card-foot{margin-top:4px;display:flex;justify-content:space-between;align-items:center;padding-left:4px}
.card-meta{font-size:5.2px;line-height:11px;color:var(--muted)}
.btn-details{width:54px;height:18px;border:1px solid var(--line);font-size:5.4px;color:#ccc;display:flex;align-items:center;justify-content:center;letter-spacing:.3px}

.pager{right:61px;top:982px;display:flex;gap:5px}
.pager span{width:15px;height:15px;border:1px solid #444;font-size:5.5px;color:#ccc;display:flex;align-items:center;justify-content:center}

/* footer */
.site-footer{left:0;top:1032px;width:737px;height:138px;background:var(--footer)}
.foot-title{font-family:"Crimson Text",serif;font-size:10px;letter-spacing:.8px}
.foot-col{font-size:5px;line-height:14.2px;color:var(--dim);letter-spacing:.4px}
.newsletter-sub{font-size:5px;color:var(--dim);letter-spacing:.3px}
.email-field{width:167px;height:18px;border:1px solid #555;font-size:5px;color:var(--dim);padding-left:8px;display:flex;align-items:center}
.btn-sub{width:60px;height:18px;border:1px solid #777;font-size:5.5px;display:flex;align-items:center;justify-content:center}
.badge{background:#444}
.bottom-bar{left:0;top:1170px;width:737px;height:30px;background:var(--bottom);display:flex;align-items:center;padding:0 67px;font-size:5px;color:var(--dim);letter-spacing:.4px}
.bottom-bar .sep{margin:0 10px}
.net{margin-left:auto;display:flex;align-items:center;gap:10px}
.net i{width:6px;height:6px;border-radius:50%;background:#777;display:block}
</style>
</head>
<body>

<header class="site-header">
  <div class="abs brand"><span class="brand-mark"></span><span class="brand-name">Kelvora Stones</span></div>
  <div class="abs shipping">
    <svg width="20" height="12" viewBox="0 0 20 12"><rect x="0" y="1" width="12" height="8" fill="#2f9a3e"/><path d="M12 4h4l3 3v2h-7z" fill="#2f9a3e"/><circle cx="4" cy="10" r="2" fill="#2f9a3e"/><circle cx="15" cy="10" r="2" fill="#2f9a3e"/></svg>
    FREE SHIPPING
  </div>
  <nav class="abs top-links"><span>MY ACCOUNT</span><span>/</span><span>LOGIN</span><span>/</span><span>REGISTER</span></nav>
  <div class="abs social-row">
    <span class="social-name">Facelink</span>
    <span class="social-name">Snapgram</span>
    <span class="phone"><svg width="8" height="8" viewBox="0 0 10 10"><path d="M2 1l2 2-1 1.5a6 6 0 0 0 2.5 2.5L7 6l2 2-1.5 1.5C4 9 1 6 .5 2.5z" fill="#8d8d8d"/></svg>(555) 730-0400</span>
    <span class="cart"><svg width="11" height="12" viewBox="0 0 11 12"><rect x="1" y="4" width="9" height="7.5" fill="none" stroke="#8d8d8d"/><path d="M3.5 4V2.5a2 2 0 0 1 4 0V4" fill="none" stroke="#8d8d8d"/></svg>CART IS : 0 ITEMS</span>
  </div>
</header>

<nav class="main-nav">
  <span>HOME</span><i class="dot"></i><span>GEMSTONES</span><i class="dot"></i><span>SHOWS</span><i class="dot"></i><span>SPECIAL GEMSTONES</span><i class="dot"></i><span>CARVINGS</span><i class="dot"></i><span>BEADS</span><i class="dot"></i><span>GOLD JEWELRY</span><i class="dot"></i><span>SILVER JEWELRY</span>
</nav>

<section>
  <div class="abs hero" role="img" aria-label="Large cut diamonds glittering on a dark reflective surface"></div>
  <div class="abs hero-title">STONES CATEGORY</div>
  <div class="abs hero-script">Kelvora Stones is a jewellery<br>online boutique</div>
  <div class="abs hero-market">Kelvora Stones on <b>Bidora</b></div>
</section>

<main>
  <h1 class="abs section-title">STONES</h1>
  <p class="abs section-intro">Kelvora Stones USA is an exciting new venture for the Kelvora Stones franchise. This dedicated sales office based in Harbor City, USA</p>

  <!-- row 1 -->
  <article class="card" style="left:61px;top:352px"><div class="card-img" role="img" aria-label="Clear cut crystal on lavender backdrop" style="background:radial-gradient(circle at 50% 55%,#f4f3fa,#a9a6c0 70%,#6f6c88)"></div><div class="card-code">ST-110-13-VO</div><div class="card-desc">1.24 CARATS NATURAL AQUAMARINE<br>LOOSE GEMSTONE - OCTAGON</div><div class="card-foot"><div class="card-meta">7.05 CARATS<br>25.4 X 25.4 MM</div><div class="btn-details">VIEW DETAILS</div></div></article>
  <article class="card" style="left:187px;top:352px"><div class="card-img" role="img" aria-label="Brilliant cut diamond on white" style="background:radial-gradient(ellipse at 50% 50%,#c9cdd2 0%,#eef0f2 40%,#fff 70%)"></div><div class="card-code">ST-110-13-VO</div><div class="card-desc">1.24 CARATS NATURAL AQUAMARINE<br>LOOSE GEMSTONE - OCTAGON</div><div class="card-foot"><div class="card-meta">7.05 CARATS<br>25.4 X 25.4 MM</div><div class="btn-details">VIEW DETAILS</div></div></article>
  <article class="card" style="left:313px;top:352px"><div class="card-img" role="img" aria-label="Several diamonds sparkling on black" style="background:radial-gradient(ellipse at 50% 65%,#5a6a80 0%,#1a2230 45%,#000 75%)"></div><div class="card-code">ST-110-13-VO</div><div class="card-desc">1.24 CARATS NATURAL AQUAMARINE<br>LOOSE GEMSTONE - OCTAGON</div><div class="card-foot"><div class="card-meta">7.05 CARATS<br>25.4 X 25.4 MM</div><div class="btn-details">VIEW DETAILS</div></div></article>
  <article class="card" style="left:438px;top:352px"><div class="card-img" role="img" aria-label="Deep blue sapphire on white" style="background:radial-gradient(ellipse at 50% 45%,#1f5db8 0%,#0b2f72 35%,#e9eef6 62%,#fff 80%)"></div><div class="card-code">ST-110-13-VO</div><div class="card-desc">1.24 CARATS NATURAL AQUAMARINE<br>LOOSE GEMSTONE - OCTAGON</div><div class="card-foot"><div class="card-meta">7.05 CARATS<br>25.4 X 25.4 MM</div><div class="btn-details">VIEW DETAILS</div></div></article>
  <article class="card" style="left:564px;top:352px"><div class="card-img" role="img" aria-label="Assorted colored gemstones on white" style="background:radial-gradient(ellipse at 50% 50%,#d8a070 0%,#c9a0c0 25%,#fff 60%)"></div><div class="card-code">ST-110-13-VO</div><div class="card-desc">1.24 CARATS NATURAL AQUAMARINE<br>LOOSE GEMSTONE - OCTAGON</div><div class="card-foot"><div class="card-meta">7.05 CARATS<br>25.4 X 25.4 MM</div><div class="btn-details">VIEW DETAILS</div></div></article>

  <!-- row 2 -->
  <article class="card" style="left:61px;top:565px"><div class="card-img" role="img" aria-label="Purple oval gem with blue stone" style="background:radial-gradient(ellipse at 40% 50%,#9a2a80 0%,#5e1450 30%,#e4e4e8 60%,#fafafa)"></div><div class="card-code">ST-110-13-VO</div><div class="card-desc">1.24 CARATS NATURAL AQUAMARINE<br>LOOSE GEMSTONE - OCTAGON</div><div class="card-foot"><div class="card-meta">7.05 CARATS<br>25.4 X 25.4 MM</div><div class="btn-details">VIEW DETAILS</div></div></article>
  <article class="card" style="left:187px;top:565px"><div class="card-img" role="img" aria-label="Scattered diamonds on dark gray" style="background:radial-gradient(ellipse at 55% 50%,#8a8a8a 0%,#3a3a3a 45%,#151515)"></div><div class="card-code">ST-110-13-VO</div><div class="card-desc">1.24 CARATS NATURAL AQUAMARINE<br>LOOSE GEMSTONE - OCTAGON</div><div class="card-foot"><div class="card-meta">7.05 CARATS<br>25.4 X 25.4 MM</div><div class="btn-details">VIEW DETAILS</div></div></article>
  <article class="card" style="left:313px;top:565px"><div class="card-img" role="img" aria-label="Pink, orange and blue cut gems on white" style="background:linear-gradient(135deg,#e0a040 0%,#f4e8ec 35%,#e06a9a 55%,#b8d0e8 80%,#fff)"></div><div class="card-code">ST-110-13-VO</div><div class="card-desc">1.24 CARATS NATURAL AQUAMARINE<br>LOOSE GEMSTONE - OCTAGON</div><div class="card-foot"><div class="card-meta">7.05 CARATS<br>25.4 X 25.4 MM</div><div class="btn-details">VIEW DETAILS</div></div></article>
  <article class="card" style="left:438px;top:565px"><div class="card-img" role="img" aria-label="Light blue diamonds on white" style="background:radial-gradient(ellipse at 50% 50%,#90a8d0 0%,#d6e0f0 35%,#fff 65%)"></div><div class="card-code">ST-110-13-VO</div><div class="card-desc">1.24 CARATS NATURAL AQUAMARINE<br>LOOSE GEMSTONE - OCTAGON</div><div class="card-foot"><div class="card-meta">7.05 CARATS<br>25.4 X 25.4 MM</div><div class="btn-details">VIEW DETAILS</div></div></article>
  <article class="card" style="left:564px;top:565px"><div class="card-img" role="img" aria-label="Diamond resting on dark rough rock" style="background:linear-gradient(180deg,#c8c8c8 0%,#8a8a8a 45%,#2e2e2e 75%,#151515)"></div><div class="card-code">ST-110-13-VO</div><div class="card-desc">1.24 CARATS NATURAL AQUAMARINE<br>LOOSE GEMSTONE - OCTAGON</div><div class="card-foot"><div class="card-meta">7.05 CARATS<br>25.4 X 25.4 MM</div><div class="btn-details">VIEW DETAILS</div></div></article>

  <!-- row 3 -->
  <article class="card" style="left:61px;top:775px"><div class="card-img" role="img" aria-label="Emerald cut aquamarine on white" style="background:radial-gradient(ellipse at 50% 50%,#5aa0a8 0%,#8cc4c8 25%,#fff 55%)"></div><div class="card-code">ST-110-13-VO</div><div class="card-desc">1.24 CARATS NATURAL AQUAMARINE<br>LOOSE GEMSTONE - OCTAGON</div><div class="card-foot"><div class="card-meta">7.05 CARATS<br>25.4 X 25.4 MM</div><div class="btn-details">VIEW DETAILS</div></div></article>
  <article class="card" style="left:187px;top:775px"><div class="card-img" role="img" aria-label="Pile of diamonds on dark surface" style="background:radial-gradient(ellipse at 50% 45%,#d8d8d8 0%,#7a7a7a 40%,#1a1a1a 80%)"></div><div class="card-code">ST-110-13-VO</div><div class="card-desc">1.24 CARATS NATURAL AQUAMARINE<br>LOOSE GEMSTONE - OCTAGON</div><div class="card-foot"><div class="card-meta">7.05 CARATS<br>25.4 X 25.4 MM</div><div class="btn-details">VIEW DETAILS</div></div></article>
  <article class="card" style="left:313px;top:775px"><div class="card-img" role="img" aria-label="Trillion cut aquamarine on white" style="background:radial-gradient(ellipse at 50% 50%,#3e8a94 0%,#7ab8bc 25%,#fff 52%)"></div><div class="card-code">ST-110-13-VO</div><div class="card-desc">1.24 CARATS NATURAL AQUAMARINE<br>LOOSE GEMSTONE - OCTAGON</div><div class="card-foot"><div class="card-meta">7.05 CARATS<br>25.4 X 25.4 MM</div><div class="btn-details">VIEW DETAILS</div></div></article>
  <article class="card" style="left:438px;top:775px"><div class="card-img" role="img" aria-label="Oval aquamarine on white" style="background:radial-gradient(ellipse at 50% 50%,#3a8088 0%,#78b0b4 28%,#fff 55%)"></div><div class="card-code">ST-110-13-VO</div><div class="card-desc">1.24 CARATS NATURAL AQUAMARINE<br>LOOSE GEMSTONE - OCTAGON</div><div class="card-foot"><div class="card-meta">7.05 CARATS<br>25.4 X 25.4 MM</div><div class="btn-details">VIEW DETAILS</div></div></article>
  <article class="card" style="left:564px;top:775px"><div class="card-img" role="img" aria-label="Tumbled amethyst pieces on white" style="background:radial-gradient(ellipse at 50% 50%,#4a2070 0%,#7a50a0 35%,#fff 70%)"></div><div class="card-code">ST-110-13-VO</div><div class="card-desc">1.24 CARATS NATURAL AQUAMARINE<br>LOOSE GEMSTONE - OCTAGON</div><div class="card-foot"><div class="card-meta">7.05 CARATS<br>25.4 X 25.4 MM</div><div class="btn-details">VIEW DETAILS</div></div></article>

  <nav class="abs pager"><span>&laquo;</span><span>01</span><span>02</span><span>03</span><span>04</span><span>&raquo;</span></nav>
</main>

<footer>
  <div class="abs site-footer"></div>
  <div class="abs foot-title" style="left:66px;top:1058px">KELVORA STONES USA</div>
  <div class="abs foot-col" style="left:67px;top:1076px">WHO WE ARE<br>OUR HISTORY<br>THE CONCEPT<br>PRODUCT SHOWCASE<br>A QUICK EDUCATION IN JEWELLERY</div>
  <div class="abs foot-col" style="left:188px;top:1076px">OUR PROCESS<br>WHERE WE OPERATE<br>OUR PROMISE<br>A QUOTATION FORM<br>OUR CONTACT</div>
  <div class="abs foot-col" style="left:283px;top:1076px">OUR LOCATION<br>FAQ'S<br>DISCLAIMERS AND LEGAL INFO<br>NEWS<br>BLOG</div>
  <div class="abs foot-title" style="left:393px;top:1058px">NEWSLETTER SIGNUP</div>
  <div class="abs newsletter-sub" style="left:393px;top:1081px">GET OUR RECENT UPDATES THROUGH YOUR EMAIL ID</div>
  <div class="abs email-field" style="left:394px;top:1096px">ENTER YOUR EMAIL ID</div>
  <div class="abs btn-sub" style="left:394px;top:1122px">SUBSCRIBE</div>
  <div class="abs badge" style="left:605px;top:1060px;width:52px;height:18px"></div>
  <div class="abs badge" style="left:594px;top:1086px;width:72px;height:24px"></div>
  <div class="abs badge" style="left:604px;top:1118px;width:52px;height:33px"></div>
  <div class="abs bottom-bar">
    <span>&copy; 2016. KELVORA STONES USA ALL RIGHTS RESERVED.</span><span class="sep">/</span><span>TERMS &amp; CONDITIONS</span><span class="sep">/</span><span>PRIVACY POLICY</span><span class="sep">/</span><span>DISCLAIMER</span>
    <span class="net">CONNECT WITH OUR SOCIAL NETWORK : <i></i><i></i><i></i><i></i><i></i></span>
  </div>
</footer>

</body>
</html>
```